Wordpress Theme for Medical Clinics

** Please view updated Sitemap2.pdf doc to clarify some confusion ***

This is a multiuser WordPress subscription site for medical clinics. Please see attachment for sitemap. Please do not include extra content like social media icons, search bars, or images. If you have questions, please ask for clarification.
The site contains the following pages and sub-pages:

1. Home
2. Our Clinic
2a. Our Clinic > Mission
2b. Our Clinic > Services
2c. Our Clinic > Clinic Policies
2d. Our Clinic > Schedules
3. Our Staff
3a. Our Staff > [Staff member page]
4. Resources
4a. Resources > Patient Health (index)
4b. Resources > Patient Health (index) > [post]
4c. Resources > Links
4d. Resources > Forms
5. Alerts
5a. Alerts > [Alert Page]
6. Contact Us

Includes the Following Pages, Subpages, and Content
1. Home
a. About Us
b. Our Staff
c. Bulletins
d. Accepting New Patients (shown as an alert widget)
e. Links
i. Physician Toolbox
ii. Book an Appointment
f. Clinic Policies
i. Show first 3 policies (e.g. Late Arrivals, Missed Appointments, Fees)
ii. Link to Clinic Policies page
g. Primary widget (displayed on all pages)
i. Hours of operation
ii. Contact Info
1. Tel
2. Fax
3. Email
4. Address
5. Get directions (link to Google Maps)
2. Our Clinic
a. Main Page
i. Clinic Name
ii. Overview
iii. Languages Spoken
iv. Secondary Navigation
1. Mission
2. Services
3. Clinic Policies
4. Schedules (see attachment)
b. Our Clinic > Mission
c. Our Clinic > Services
i. For each service include service TITLE and DESCRIPTION
d. Our Clinic > Clinic Policies
i. For each policy include policy TITLE and DESCRIPTION
ii. Include the following policies in mockup
1. Late arrivals
2. Missed appointments
3. Fees for missed appointments
4. Referrals and follow-ups
5. Services not covered by RDA
6. Information for LTF patients
7. Medical Legal Reports
e. Our Clinic > Schedules
3. Our Staff
a. Main Page
i. Display a list of staff members. Include NAME and DESIGNATION
b. Our Staff > [Staff Name]
i. Include NAME, PICTURE, DESIGNATION, and BIO
4. Resources
a. Resources > Patient Health
i. Main Page
1. Posts (ordered by date)
a. Title
b. Summary
2. Side Navigation
a. Post Categories
ii. Patient Health > [post title]
1. Title
2. Post Category
3. Date
4. Author
5. Summary
6. Body
b. Resources > Links
1. Secondary Navigation - Categories
a. Sample Categories:
i. Local Services
ii. RDA and Drug Coverage
iii. Mental Health Resources
2. Category page
a. Include the following links in the 'Local Services' category
i. Hypertension clinics
ii. Home Care services
iii. Vaccine Clinics
c. Resources > Forms
i. Display a table with form TITLE and CATEGORY
ii. Side Navigation
1. Form Categories
a. Use the following sample Categories
i. Referrals
ii. Insurance
iii. Intake
iv. Discharge
v. Waivers
5. Alerts
a. Main page
i. List of all Alert posts
1. Include post TITLE as a link to the post
ii. Side Navigation
1. Alerts Archive
a. shown as Month + Number of posts
iii. Alerts > [Alert page]
1. Include TITLE, DATE, AUTHOR, BODY
6. Contact Us
a. Map
b. Hours of operation
c. Address
d. Phone number
e. Fax number
e. Fax number
f. Map
g. Email

Design notes:
- fixed width
- responsive (need designs for mobile, tablet, and desktop)
- simple, dark font, white background
- use Font Awesome icons where needed
- user adds own logo

Target Market(s)

Medical Clinics

Industry/Entity Type

Medical

Number of Pages Required

5+ page

Font styles to use
Serif
Sans Serif

Requirements
Must have
• Please keep designs very simple.
• Examples:
• https://www.quolbin.com/install
• http://www.ventrohax.com/company/about-us
• http://brindlequota.org/
• http://www.trosk.com/
Should not have
• Minimal or no use of shadows and gradients

```html
<!DOCTYPE html>
<html lang="en">
<head>
<meta charset="utf-8">
<title>Medical Clinics – Forms</title>
<link href="https://fonts.googleapis.com/css2?family=Open+Sans:wght@400;600;700&display=swap" rel="stylesheet">
<style>
:root{
  --blue:#0a8ce2;
  --text:#333333;
  --muted:#6f6f6f;
  --band:#f8f8f8;
  --panel:#f2f2f2;
  --line:#d6d6d6;
  --footer:#252525;
  --footer-text:#8a8a8a;
  --white:#ffffff;
}
*{box-sizing:border-box;margin:0;padding:0}
html,body{width:1200px;height:1110px;overflow:hidden}
body{font-family:"Open Sans",sans-serif;color:var(--text);background:var(--white);position:relative;font-size:10px}
a{color:inherit;text-decoration:none}
.abs{position:absolute}

.topbar{left:0;top:0;width:1200px;height:30px;background:var(--blue);color:var(--white);font-size:9.5px}
.topbar .help{left:161px;top:9px}
.topbar .help .sep{display:inline-block;width:1px;height:14px;background:var(--white);vertical-align:middle;margin:0 4px}
.topbar .quick{right:161px;top:9px}
.topbar .quick .sep{display:inline-block;width:1px;height:14px;background:var(--white);vertical-align:middle;margin:0 6px}

.header{left:0;top:30px;width:1200px;height:83px}
.brand{left:162px;top:22px;display:flex;align-items:center;gap:14px}
.brand-mark{width:30px;height:30px;border-radius:50%;background:var(--blue)}
.brand-name{font-size:21px;font-weight:600;color:var(--text)}
.mainnav{left:551px;top:0;height:83px;display:flex}
.mainnav a{display:flex;align-items:center;height:83px;padding:0 20px;font-size:10.5px;color:var(--text)}
.mainnav a.active{background:var(--blue);color:var(--white);padding:0 6px;margin:0 14px 0 0}

.crumbs{left:0;top:113px;width:1200px;height:59px;background:var(--band)}
.crumbs h1{position:absolute;left:162px;top:16px;font-size:10px;font-weight:700;text-transform:uppercase}
.crumbs p{position:absolute;left:162px;top:35px;font-size:9.5px;text-transform:uppercase}

.forms{left:161px;top:208px;width:652px;height:612px;background:var(--panel);border:1px solid var(--line)}
.box-head{background:var(--blue);color:var(--white);font-weight:700;text-transform:uppercase}
.forms .box-head{height:32px;padding:8px 12px;font-size:13px}
.search{position:absolute;left:75px;top:55px;display:flex}
.search input{width:385px;height:36px;border:1px solid #e2e2e2;background:var(--white);padding:0 13px;font-family:inherit;font-size:9.5px;color:var(--muted)}
.search button{width:117px;height:36px;border:0;background:var(--blue);color:var(--white);font-family:inherit;font-weight:700;font-size:10.5px}
.forms-table{position:absolute;left:0;top:114px;width:650px;border-collapse:collapse;font-size:9.5px}
.forms-table th{height:23px;color:var(--blue);font-weight:600;text-align:left;background:var(--white)}
.forms-table td{height:22.5px}
.forms-table tbody tr:nth-child(odd) td{background:#f4f4f4}
.forms-table tbody tr:nth-child(even) td{background:var(--white)}
.forms-table .num{width:75px;text-align:center;border-right:1px solid #c9c9c9}
.forms-table .title{width:375px;padding-left:18px;border-right:1px solid #c9c9c9}
.forms-table .cat{padding-left:19px}
.forms-table tr.blank td{height:22px;background:var(--white)}
.pager{position:absolute;left:112px;top:563px;display:flex;border:1px solid #cfcfcf;background:var(--white);border-radius:2px}
.pager span{width:44px;height:28px;display:flex;align-items:center;justify-content:center;font-size:9.5px;border-left:1px solid #cfcfcf}
.pager span:first-child{border-left:0;width:38px}
.pager span:last-child{width:38px}

.side{left:836px;width:203px;border:1px solid var(--line);background:var(--white)}
.side .box-head{height:33px;padding:10px 13px;font-size:10px}
.cats{top:210px;height:150px}
.cats ul{list-style:none;padding:11px 14px 0}
.cats li{display:flex;justify-content:space-between;height:18px;font-size:9.5px}
.cats li.current{color:var(--blue)}
.hours{top:381px;height:360px}
.hours .intro{padding:9px 14px 0;font-size:9.5px;line-height:14px}
.hours dl,.contact dl{display:grid;padding:0 14px;font-size:9.5px}
.hours dl{grid-template-columns:90px 1fr;row-gap:4px;margin-top:9px;line-height:14px}
.hours hr{border:0;border-top:1px solid #cfcfcf;margin:24px 14px 19px}
.hours h3{padding:0 14px;font-size:10px;font-weight:700;text-transform:uppercase;margin-bottom:8px}
.contact dl{grid-template-columns:94px 1fr;line-height:15px}

.footer{left:0;top:883px;width:1200px;height:227px;background:var(--footer);border-top:4px solid var(--blue);color:var(--footer-text)}
.footer .brand{top:34px}
.footer .brand-name{color:var(--white)}
.footer .about{position:absolute;left:162px;top:88px;width:205px;font-size:8.5px;line-height:13.5px;color:#c9c9c9}
.fcol{position:absolute;top:34px}
.fcol h4{font-size:12px;font-weight:600;color:#9a9a9a;margin-bottom:6px}
.fcol ul{list-style:none;font-size:9.5px;line-height:18px}
.fcol li.on{color:#cfcfcf}
.fcol dl{display:grid;grid-template-columns:89px 1fr;font-size:9.5px;line-height:15px;margin-left:2px}
.fbottom{position:absolute;left:0;top:188px;width:1200px;border-top:1px solid #3c3c3c;font-size:9.5px}
.fbottom span{position:absolute;top:12px}
</style>
</head>
<body>

<div class="abs topbar">
  <div class="abs help">To help Here : 555 010 4477<span class="sep"></span>Email : hello@ maplecare.ca</div>
  <div class="abs quick"><a href="#">Book an Appointment</a><span class="sep"></span><a href="#">Physician Toolbox</a></div>
</div>

<header class="abs header">
  <div class="abs brand"><span class="brand-mark"></span><span class="brand-name">Medical Clinics</span></div>
  <nav class="abs mainnav">
    <a href="#">Home</a><a href="#">Our Clinic</a><a href="#">Our Staff</a><a href="#" class="active">Resources</a><a href="#">Alerts</a><a href="#">Contact Us</a>
  </nav>
</header>

<div class="abs crumbs">
  <h1>Resources</h1>
  <p>Home / Resources/Form</p>
</div>

<section class="abs forms">
  <div class="box-head">Forms</div>
  <form class="search"><input type="text" placeholder="Search forms here..."><button type="button">SEARCH</button></form>
  <table class="forms-table">
    <thead><tr><th class="num">#</th><th class="title">Title Name:</th><th class="cat">Category</th></tr></thead>
    <tbody>
      <tr><td class="num">1</td><td class="title">Referrals form1</td><td class="cat">Referrals</td></tr>
      <tr><td class="num">2</td><td class="title">Insurance forms 2</td><td class="cat">Insurance</td></tr>
      <tr><td class="num">3</td><td class="title">Intake forms 5</td><td class="cat">Intake</td></tr>
      <tr><td class="num">4</td><td class="title">Discharge form 1</td><td class="cat">Discharge</td></tr>
      <tr><td class="num">5</td><td class="title">Waivers forms 3</td><td class="cat">Waivers</td></tr>
      <tr><td class="num">6</td><td class="title">Hypertension clinics forms 4</td><td class="cat">Referrals</td></tr>
      <tr><td class="num">7</td><td class="title">Home Care services forms 6</td><td class="cat">Insurance</td></tr>
      <tr><td class="num">8</td><td class="title">Vaccine Clinics form 1</td><td class="cat">Intake</td></tr>
      <tr><td class="num">9</td><td class="title">Referrals form1</td><td class="cat">Discharge</td></tr>
      <tr><td class="num">10</td><td class="title">Insurance forms 2</td><td class="cat">Waivers</td></tr>
      <tr><td class="num">11</td><td class="title">Intake forms 5</td><td class="cat">Referrals</td></tr>
      <tr><td class="num">12</td><td class="title">Discharge form 1</td><td class="cat">Insurance</td></tr>
      <tr><td class="num">13</td><td class="title">Waivers forms 3</td><td class="cat">Intake</td></tr>
      <tr><td class="num">14</td><td class="title">Hypertension clinics forms 4</td><td class="cat">Discharge</td></tr>
      <tr><td class="num">15</td><td class="title">Home Care services forms 6</td><td class="cat">Waivers</td></tr>
      <tr><td class="num">16</td><td class="title">Vaccine Clinics form 1</td><td class="cat">Referrals</td></tr>
      <tr><td class="num">17</td><td class="title">Referrals form1</td><td class="cat">Insurance</td></tr>
      <tr class="blank"><td class="num"></td><td class="title"></td><td class="cat"></td></tr>
    </tbody>
  </table>
  <nav class="pager">
    <span>&lsaquo;</span><span>1</span><span>2</span><span>3</span><span>4</span><span>5</span><span>6</span><span>7</span><span>8</span><span>&rsaquo;</span>
  </nav>
</section>

<aside class="abs side cats">
  <div class="box-head">Categories</div>
  <ul>
    <li><span>Referrals</span><span>(8)</span></li>
    <li class="current"><span>Insurance</span><span>(20)</span></li>
    <li><span>Intake</span><span>(5)</span></li>
    <li><span>Discharge</span><span>(9)</span></li>
    <li><span>Waivers</span><span>(35)</span></li>
  </ul>
</aside>

<aside class="abs side hours">
  <div class="box-head">Hours of Opration</div>
  <p class="intro">Lorem Ipsum is simply dummy text of the printing and typesetting</p>
  <dl>
    <dt>Monday :</dt><dd>8:00 AM - 6:00 PM</dd>
    <dt>Tuesday :</dt><dd>8:00 AM - 6:00 PM</dd>
    <dt>Wednesday :</dt><dd>8:00 AM - 6:00 PM</dd>
    <dt>Thursday :</dt><dd>8:00 AM - 6:00 PM</dd>
    <dt>Friday :</dt><dd>8:00 AM - 6:00 PM</dd>
    <dt>Saturday :</dt><dd>9:00 AM - 4:00 PM</dd>
    <dt>Sunday :</dt><dd>9:00 AM - 4:00 PM</dd>
  </dl>
  <hr>
  <div class="contact">
    <h3>Contact Info</h3>
    <dl>
      <dt>Telephone :</dt><dd>250-555-0188</dd>
      <dt>Email:</dt><dd>hello@maplecare.ca</dd>
      <dt>Address:</dt><dd>48 Alder Road<br>Kelowna,B.<br>Canada, V2X 4KD</dd>
    </dl>
  </div>
</aside>

<footer class="abs footer">
  <div class="abs brand"><span class="brand-mark"></span><span class="brand-name">Medical Clinics</span></div>
  <p class="about">Lorem Ipsum is simply dummy text of the printing and typesetting industry. Lorem Ipsum has been the industry's standard dummy text</p>
  <div class="fcol" style="left:461px">
    <h4>Navigation</h4>
    <ul><li class="on">Home</li><li>Our Clinic</li><li>Newsletter</li><li>Our Staff</li><li>Resources</li></ul>
  </div>
  <div class="fcol" style="left:686px">
    <h4>Links</h4>
    <ul><li>Help</li><li>Support</li><li>Privacy Policy</li></ul>
  </div>
  <div class="fcol" style="left:836px">
    <h4>Contact Us</h4>
    <dl>
      <dt>Telephone :</dt><dd>250-555-0188</dd>
      <dt>Email:</dt><dd>hello@maplecare.ca</dd>
      <dt>Address:</dt><dd>48 Alder Road<br>Kelowna,B. Canada,<br>V2X 4KD</dd>
    </dl>
  </div>
  <div class="fbottom">
    <span style="left:162px">© 2015 Medical Clinces. All Rights Reservsd</span>
    <span style="left:463px">About Us</span>
    <span style="left:530px">Terms of Use</span>
    <span style="left:614px">Privacy Policy</span>
  </div>
</footer>

</body>
</html>
```